Public Adjusters Collective Business card

We need to get business card Design for our Company we are Public Adjusters in Chicago Illinois - i like to see good combination and elements from my Company Logo. as well To be an two side design
Updates

Target Market(s)

Home /Business owner Property Managers

Industry/Entity Type

Business

Contact Information for Business Card

to show the Element of our logo i will Like 3D

Font styles to use
Sans Serif

Requirements
Must have
• Logo and Element of the Logo in 3D
Nice to have
• Logo That we Provide 3D Same Colors or open for suggestions
Should not have
• unleare view -

```html
<!DOCTYPE html>
<html lang="en">
<head>
<meta charset="utf-8">
<title>Public Adjusters Collective – Business Card</title>
<link rel="stylesheet" href="https://fonts.googleapis.com/css2?family=Roboto:wght@400;500;700&display=swap">
<style>
  :root {
    --stage: #4a4a4a;
    --navy-deep: #0f0c45;
    --royal: #1a3fd6;
    --accent: #e2452c;
    --ink-light: #ffffff;
    --brand-blue: #2a4fc4;
    --card-white: #f7f7f7;
  }
  html, body {
    margin: 0;
    padding: 0;
    overflow: hidden;
  }
  body {
    width: 1200px;
    height: 750px;
    background: var(--stage);
    position: relative;
    font-family: "Roboto", sans-serif;
  }
  .card {
    position: absolute;
    box-sizing: border-box;
  }
  .card-front {
    left: 210px;
    top: 144px;
    width: 264px;
    height: 461px;
    background: radial-gradient(ellipse 75% 55% at 50% 45%, var(--royal) 0%, #1230a8 35%, #111a6e 70%, var(--navy-deep) 100%);
    color: var(--ink-light);
    text-align: center;
  }
  .holder-name {
    margin: 0;
    padding-top: 38px;
    font-size: 17px;
    font-weight: 500;
    color: var(--accent);
    letter-spacing: 0.3px;
  }
  .holder-title {
    margin: 1px 0 0;
    font-size: 13px;
  }
  .address {
    margin: 14px 0 0;
    font-size: 12px;
    line-height: 16px;
    font-style: normal;
  }
  .contact-list {
    list-style: none;
    margin: 6px 0 0;
    padding: 0;
    font-size: 12px;
    line-height: 17.6px;
  }
  .contact-list .label {
    color: var(--accent);
    margin-right: 3px;
  }
  .front-brand {
    position: absolute;
    left: 0;
    right: 0;
    top: 232px;
    height: 229px;
    display: flex;
    align-items: center;
    justify-content: center;
  }
  .front-brand .brand-name {
    font-size: 18px;
    font-weight: 700;
    color: var(--ink-light);
    line-height: 24px;
    padding: 0 30px;
  }
  .card-back {
    left: 523px;
    top: 338px;
    width: 462px;
    height: 263px;
    background: var(--card-white);
    display: flex;
    align-items: center;
    justify-content: center;
  }
  .card-back .brand-name {
    font-size: 19px;
    font-weight: 700;
    color: var(--brand-blue);
  }
</style>
</head>
<body>
  <section class="card card-front" aria-label="Business card front">
    <h1 class="holder-name">MARLA VENN</h1>
    <p class="holder-title">President</p>
    <address class="address">4127 Harlow Crescent<br>Brightwater, IL 60917</address>
    <ul class="contact-list">
      <li><span class="label">P :</span>555 0142 3318</li>
      <li><span class="label">M :</span>555 0187 6624</li>
      <li><span class="label">F :</span>555 0163 9071</li>
      <li><span class="label">E :</span>marla@qpacollective.com</li>
      <li><span class="label">W :</span>www.qpacollective.com</li>
    </ul>
    <div class="front-brand">
      <div class="brand-name">Public Adjusters Collective</div>
    </div>
  </section>

  <section class="card card-back" aria-label="Business card back">
    <div class="brand-name">Public Adjusters Collective</div>
  </section>
</body>
</html>
```